Website for Vornelix Capital, my new firm that raises money from investors to buy, build, own an...

Vornelix Capital needs a website! We are a new company with very experienced people, who invest in, own and build hotel properties, as well as apartments and other commercial real estate. We seek investors for our projects, and we provide safe, secure returns on their investment in our projects. Our new logo is designed to exhibit strength, class and security, and would like our website to continue on this theme. Our name, Vornelix, is a word-play on a Greek word “aristeia”, which means “excellence” and “a warriors finest moment of glory in war”. If you are in business, you realize that much of it is like war, with strategy and moves and opponents and competitors, and ever-changing economic conditions and threats that make business very much like war. We like to think that we are good at business (war), and so have named our company “Vornelix”, using the founders last name and the word “aristeia” combined. Another definition of "aristeia" is "performing at the peak of one's potential after a long struggle"...again, much like business in real life! The website design should exhibit financial security, smart moves, and positive growth towards a bright future.

Target Market(s)

The target market is smart and wealthy investors, with others such as brokers, cities and government agencies, lenders, sellers, partners, etc also looking at it.

Industry/Entity Type

Investment

Number of Pages Required

5+ page

Font styles to use
Sans Serif

Colors
fec214

Requirements
Must have
• Our website should have a landing page, a "about" or bio page, a projects page and a contact us page. Our new logo uses the colors black and gold, so this should be factored in to our site. The site should be simple, yet impactful and impressive. I have actually two logos, which can be mixed and interchanged in a complimentary way, each with their own unique look.
Nice to have
• I have uploaded a couple screenshots of a website i like, and the simplicity I mention.
Should not have
• The site should not be flashy or complicated or complex or "busy"

```html
<!DOCTYPE html>
<html lang="en">
<head>
<meta charset="UTF-8">
<title>Vornelix Capital</title>
<link rel="stylesheet" href="https://fonts.googleapis.com/css2?family=Nunito+Sans:wght@400;600;700;800&display=swap">
<style>
:root{
  --gold:#fec214;
  --gold-deep:#d9a21a;
  --gold-dark:#b98612;
  --ink:#1c1c1c;
  --text:#3a3a3a;
  --muted:#666;
  --hero-bg:#f1f2f4;
  --line:#c9ccd2;
  --white:#fff;
  --dark:#2b2d30;
}
*{box-sizing:border-box;margin:0;padding:0}
html,body{width:1200px;height:2769px;overflow:hidden}
body{font-family:"Nunito Sans",Arial,sans-serif;color:var(--ink);background:var(--white);position:relative}
.section{position:absolute;left:0;width:1200px}
.center-text{position:absolute;left:0;width:1200px;text-align:center}

/* header & hero */
.hero{top:0;height:633px;background:var(--hero-bg);overflow:hidden}
.hero-skyline{position:absolute;left:350px;top:155px;width:822px;height:478px;background:linear-gradient(180deg,rgba(201,204,210,0) 0%,rgba(201,204,210,.35) 55%,rgba(201,204,210,.55) 100%)}
.brand{position:absolute;left:100px;top:70px;display:flex;align-items:center;gap:14px}
.brand-mark{width:30px;height:30px;background:var(--gold)}
.brand-name{font-size:34px;font-weight:800;color:var(--ink);letter-spacing:1px;text-transform:uppercase;line-height:1}
.main-nav{position:absolute;left:511px;top:79px;display:flex;height:43px;border:1px solid #8a8a8a;background:var(--white)}
.nav-item{display:flex;align-items:center;justify-content:center;height:41px;font-size:17px;font-weight:700;color:var(--ink);text-decoration:none;border-left:1px solid #8a8a8a;text-transform:uppercase}
.nav-item:first-child{border-left:none;background:var(--gold);color:var(--white)}
.nav-home{width:120px}.nav-about{width:131px}.nav-projects{width:160px}.nav-contact{width:177px}
.hero-title{top:222px;font-size:62px;font-weight:800;letter-spacing:1px}
.hero-lead{top:310px;font-size:20px;line-height:34px;color:var(--text)}
.btn{position:absolute;display:flex;align-items:center;justify-content:center;font-size:16px;font-weight:800;text-transform:uppercase;text-decoration:none;letter-spacing:.5px}
.btn-gold{left:510px;width:180px;height:48px;border:2px solid var(--gold);color:var(--gold)}
.btn-work{top:415px;background:rgba(255,255,255,.4)}
.scroll-cue{position:absolute;left:580px;top:548px}

/* welcome */
.welcome{top:633px;height:545px;background:linear-gradient(160deg,#f3b51d 0%,var(--gold-deep) 45%,#c9931a 70%,var(--gold-dark) 100%);overflow:hidden}
.welcome-title{top:82px;font-size:60px;font-weight:800;line-height:66px;color:var(--white);letter-spacing:1px}
.welcome-text{top:238px;left:200px;width:800px;font-size:14.5px;line-height:27px;color:rgba(255,255,255,.88);text-align:center;position:absolute}
.btn-white{left:524px;top:392px;width:152px;height:51px;border:2px solid var(--white);color:var(--white);font-size:17px}

/* projects */
.projects-section{top:1178px;height:779px;background:var(--white)}
.projects-title{top:80px;font-size:62px;font-weight:800}
.card{position:absolute;top:195px;width:314px}
.card-frame{height:200px;border:1px solid #a9a9a9;padding:16px 14px 0 16px}
.card-photo{height:184px;width:282px}
.photo-1{background:linear-gradient(180deg,#2f55d6 0%,#7a9fe6 45%,#e8edf3 70%,#5c7d4d 100%)}
.photo-2{background:linear-gradient(180deg,#5b92e0 0%,#b9d3ef 40%,#6d90b3 70%,#4f7a3c 100%)}
.photo-3{background:linear-gradient(180deg,#213a8e 0%,#4a5fa8 40%,#a9774a 70%,#2c2a2e 100%)}
.card-body{margin-left:16px;width:282px;height:181px;border:1px solid #bdbdbd;border-top:none;padding:16px 12px 0 18px}
.card-title{font-size:23px;font-weight:700;color:var(--ink);line-height:30px}
.card-text{margin-top:8px;font-size:14.5px;line-height:24px;color:var(--muted)}
.card-link{display:block;margin-top:12px;font-size:15px;font-weight:800;color:var(--gold);text-decoration:none}
.btn-more{top:635px}

/* contact */
.contact-section{top:1957px;height:498px;background:linear-gradient(100deg,#3a3c3f 0%,#2a2b2e 40%,#4a4c50 70%,#2f3033 100%)}
.contact-title{top:58px;font-size:62px;font-weight:800;color:var(--white)}
.field{position:absolute;height:40px;background:var(--white);font-size:15px;color:#444;padding:10px 16px}
.field-msg{height:81px}
.submit{position:absolute;left:537px;top:376px;width:126px;height:50px;border:2px solid var(--white);border-radius:25px;color:var(--white);font-size:17px;font-weight:800;display:flex;align-items:center;justify-content:center;letter-spacing:.5px}

/* footer */
.footer{top:2455px;height:314px;background:var(--white)}
.social{position:absolute;top:82px;width:52px;height:52px;border:1.5px solid #9a9a9a;border-radius:50%}
.footer-info{top:170px;font-size:15px;color:#555;display:flex;justify-content:center;align-items:center;gap:10px}
.footer-info svg{vertical-align:middle;margin-right:6px}
.footer-links{top:210px;font-size:15px;color:#555;word-spacing:2px}
.footer-copy{top:247px;font-size:15px;color:#555}
</style>
</head>
<body>

<header class="section hero">
  <div class="hero-skyline" role="img" aria-label="Light line illustration of a city skyline with towers and clouds"></div>
  <div class="brand"><span class="brand-mark"></span><span class="brand-name">Vornelix Capital</span></div>
  <nav class="main-nav">
    <a class="nav-item nav-home" href="#">Home</a>
    <a class="nav-item nav-about" href="#">About</a>
    <a class="nav-item nav-projects" href="#">Projects</a>
    <a class="nav-item nav-contact" href="#">Contact Us</a>
  </nav>
  <h1 class="center-text hero-title">VORNELIX CAPITAL</h1>
  <p class="center-text hero-lead">We are a new company with very experienced people, who invest in, own and build hotel<br>properties, as well as apartments and other commercial real estate.</p>
  <a class="btn btn-gold btn-work" href="#">Work With Us</a>
  <svg class="scroll-cue" width="40" height="24" viewBox="0 0 40 24"><path d="M3 3 L20 19 L37 3" fill="none" stroke="#333" stroke-width="4"/></svg>
</header>

<section class="section welcome" role="img" aria-label="Upward view of glass skyscrapers in gold tones">
  <h2 class="center-text welcome-title">WELCOME TO<br>VORNELIX CAPITAL</h2>
  <p class="welcome-text">Sed ut perspiciatis unde omnis iste natus error sit voluptatem accusantium doloremque laudantium, totam rem aperiam, eaque ipsa quae ab illo inventore veritatis et quasi architecto beatae vitae dicta sunt explicabo. Nemo enim ipsam voluptatem quia voluptas sit aspernatur aut odit aut fugit, sed quia consequuntur magni dolores eos qui rati one voluptatem sequi nesciu que porro quisquam quis nostrum exercitationem ullam cor.</p>
  <a class="btn btn-white" href="#">About Us</a>
</section>

<section class="section projects-section">
  <h2 class="center-text projects-title">PROJECTS</h2>
  <article class="card" style="left:100px">
    <div class="card-frame"><div class="card-photo photo-1" role="img" aria-label="White high-rise hotel with palm trees under blue sky"></div></div>
    <div class="card-body">
      <h3 class="card-title">Finibus Bonor Malo</h3>
      <p class="card-text">Nemo enim ipsam voluptatem quiavol uptas sit aspernatur aut odit aut fugit, sed quia consequuntur..</p>
      <a class="card-link" href="#">READ MORE</a>
    </div>
  </article>
  <article class="card" style="left:443px">
    <div class="card-frame"><div class="card-photo photo-2" role="img" aria-label="Modern glass office building with trees"></div></div>
    <div class="card-body">
      <h3 class="card-title">Finibus Bonor Malo</h3>
      <p class="card-text">Nemo enim ipsam voluptatem quiavol uptas sit aspernatur aut odit aut fugit, sed quia consequuntur..</p>
      <a class="card-link" href="#">READ MORE</a>
    </div>
  </article>
  <article class="card" style="left:788px">
    <div class="card-frame"><div class="card-photo photo-3" role="img" aria-label="Lit apartment buildings at dusk"></div></div>
    <div class="card-body">
      <h3 class="card-title">Finibus Bonor Malo</h3>
      <p class="card-text">Nemo enim ipsam voluptatem quiavol uptas sit aspernatur aut odit aut fugit, sed quia consequuntur..</p>
      <a class="card-link" href="#">READ MORE</a>
    </div>
  </article>
  <a class="btn btn-gold btn-more" href="#">View More</a>
</section>

<section class="section contact-section" role="img" aria-label="Dim office meeting room with a business team">
  <h2 class="center-text contact-title">CONTACT US</h2>
  <div class="field" style="left:258px;top:160px;width:335px">First Name</div>
  <div class="field" style="left:607px;top:160px;width:335px">Last Name</div>
  <div class="field" style="left:258px;top:214px;width:335px">Email Address</div>
  <div class="field" style="left:607px;top:214px;width:335px">Phone Number</div>
  <div class="field field-msg" style="left:258px;top:266px;width:684px">Message</div>
  <div class="submit">SUBMIT</div>
</section>

<footer class="section footer">
  <span class="social" style="left:482px"></span>
  <span class="social" style="left:539px"></span>
  <span class="social" style="left:598px"></span>
  <span class="social" style="left:655px"></span>
  <div class="center-text footer-info">
    <span><svg width="12" height="16" viewBox="0 0 12 16"><path d="M6 0C2.7 0 0 2.6 0 5.8 0 10 6 16 6 16s6-6 6-10.2C12 2.6 9.3 0 6 0zm0 8a2.2 2.2 0 1 1 0-4.4A2.2 2.2 0 0 1 6 8z" fill="#fec214"/></svg>1475 Halvern Ridge Lane, Oakmere, MO 63990</span>
    <span>|</span>
    <span><svg width="15" height="15" viewBox="0 0 16 16"><path d="M3.5 1l2.5 3-1.5 2c1 2 2.5 3.5 4.5 4.5l2-1.5 3 2.5-1.5 2.5C7 15 1 9 1 2.5z" fill="#fec214"/></svg>1 555 014 2277</span>
    <span>|</span>
    <span><svg width="17" height="13" viewBox="0 0 17 13"><rect width="17" height="13" rx="1" fill="#fec214"/><path d="M1 1.5l7.5 6 7.5-6" fill="none" stroke="#fff" stroke-width="1.4"/></svg>info@vornelixcapital.com</span>
  </div>
  <div class="center-text footer-links">Help &nbsp; | &nbsp; FAQ &nbsp; | &nbsp; Support &nbsp; | &nbsp; Sitemap &nbsp; | &nbsp; Terms Of Use &nbsp; | &nbsp; Privacy Statement</div>
  <div class="center-text footer-copy">Vornelix capital. © 2018 All rights reserved.</div>
</footer>

</body>
</html>
```